Business Card Design using new attached logo

We are a family run Plumbing and Heating firm looking to improve our company image with an improved business card and new logo.We are looking to keep the company colour (Blue) involved in our design

Reason: New logo added which needs to be incorporated on designs

Industry/Entity Type

Business

Contact Information for Business Card

See attachment of all info required.

Requirements
Must have
• We have just picked a new company logo which is attached.
• Could you please provide your business card designs using this logo.
• We are looking for the logo on the back as well as the front with all the info required

```html
<!DOCTYPE html>
<html lang="en">
<head>
<meta charset="utf-8">
<title>KBN Services Ltd — Business Cards</title>
<link rel="stylesheet" href="https://fonts.googleapis.com/css2?family=Cinzel:wght@400;600&family=Open+Sans:wght@400;700&display=swap">
<style>
  :root {
    --backdrop: #e6e6e4;
    --brand-blue: #1a4fd8;
    --brand-blue-deep: #0a2c96;
    --card-white: #ffffff;
    --ink: #2a2a2a;
    --rule: #b9b9b9;
    --on-blue: #f2f2f2;
  }
  * { box-sizing: border-box; margin: 0; padding: 0; }
  html, body {
    width: 1200px; height: 871px; overflow: hidden;
    background: var(--backdrop);
  }
  .canvas { position: relative; width: 1200px; height: 871px; }

  .card {
    position: absolute; width: 540px; height: 309px;
    border-radius: 3px;
    box-shadow: 0 10px 28px rgba(0,0,0,0.22);
  }

  /* Back of card */
  .card-back {
    left: 50px; top: 140px;
    background: linear-gradient(160deg, var(--brand-blue) 0%, var(--brand-blue-deep) 100%);
    display: flex; align-items: center; justify-content: center;
  }
  .brand { display: flex; align-items: center; gap: 12px; }
  .brand-square { width: 34px; height: 34px; flex: none; }
  .card-back .brand-square { background: var(--on-blue); }
  .brand-name {
    font-family: "Cinzel", serif; font-weight: 400;
    font-size: 30px; letter-spacing: 1.5px; white-space: nowrap;
  }
  .card-back .brand-name { color: var(--on-blue); }

  /* Front of card */
  .card-front {
    left: 610px; top: 420px;
    background: var(--card-white);
    padding: 26px 30px 0 30px;
  }
  .card-front .brand-square { background: var(--brand-blue); width: 30px; height: 30px; }
  .card-front .brand-name { color: var(--brand-blue); font-size: 26px; }

  .person { margin-top: 20px; }
  .person-name {
    font-family: "Cinzel", serif; font-weight: 600;
    font-size: 17px; color: var(--ink); letter-spacing: 1px;
  }
  .person-role {
    font-family: "Cinzel", serif; font-weight: 400;
    font-size: 13px; color: var(--brand-blue); letter-spacing: 1px;
    margin-top: 1px;
  }
  .divider { height: 1px; background: var(--rule); margin: 8px 0 0 0; }

  .address {
    font-family: "Open Sans", sans-serif; font-size: 11px;
    color: var(--ink); line-height: 1.7; margin-top: 12px;
  }
  .address strong { font-weight: 700; }

  .contact {
    position: absolute; right: 30px; bottom: 22px;
    font-family: "Open Sans", sans-serif; font-size: 11.5px; color: var(--ink);
    border-top: 1px solid var(--rule); padding-top: 6px;
  }
  .contact-row {
    display: flex; justify-content: flex-end; align-items: center;
    gap: 10px; height: 19px;
  }
  .contact-row svg { width: 13px; height: 13px; flex: none; }
  .icon { fill: none; stroke: var(--brand-blue); stroke-width: 1.6; stroke-linejoin: round; stroke-linecap: round; }
</style>
</head>
<body>
<main class="canvas">

  <section class="card card-back" aria-label="Card back">
    <div class="brand">
      <span class="brand-square"></span>
      <span class="brand-name">KBN Services Ltd</span>
    </div>
  </section>

  <section class="card card-front" aria-label="Card front">
    <div class="brand">
      <span class="brand-square"></span>
      <span class="brand-name">KBN Services Ltd</span>
    </div>

    <div class="person">
      <p class="person-name">Mark Ellison</p>
      <p class="person-role">Director</p>
    </div>
    <div class="divider"></div>

    <address class="address" style="font-style:normal">
      <strong>KBN SERVICES LTD</strong><br>
      14 Mill Parade<br>
      elm road, sutton, surrey
    </address>

    <div class="contact">
      <div class="contact-row">
        <span>020 7946 0123</span>
        <svg viewBox="0 0 16 16" aria-label="Telephone"><path class="icon" d="M2 6c0-2 3-3 6-3s6 1 6 3l-3 1-1-2H6L5 7 2 6zM4 8h8l1 5H3l1-5z"/></svg>
      </div>
      <div class="contact-row">
        <span>020 7946 0456</span>
        <svg viewBox="0 0 16 16" aria-label="Fax"><path class="icon" d="M4 6V2h8v4M2 6h12v6H2zM4 10h8v4H4z"/></svg>
      </div>
      <div class="contact-row">
        <span>07700 900321</span>
        <svg viewBox="0 0 16 16" aria-label="Mobile"><path class="icon" d="M5 1h6v14H5zM7 12.5h2"/></svg>
      </div>
      <div class="contact-row">
        <span>markellison@kbnservicesltd.co.uk</span>
        <svg viewBox="0 0 16 16" aria-label="Email"><path class="icon" d="M1.5 3.5h13v9h-13zM1.5 3.5 8 9l6.5-5.5"/></svg>
      </div>
    </div>
  </section>

</main>
</body>
</html>
```